Corvane Capital Business Cards

These are professional business cards that are for my family office.
Put fake emails and phone numbers as of now until I finalize those components. This family office controls my families investments, assets, and future. The cards should be professional.
..
.
.
.
I just uploaded another variation of a logo I would like to see as a business card to I am inbeteen which logo to use

Target Market(s)

business

Industry/Entity Type

business

Contact Information for Business Card

Professional, wealth related, finance related.

Requirements
Must have
• Logo

```html
<!DOCTYPE html>
<html lang="en">
<head>
<meta charset="utf-8">
<title>Corvane Capital Business Cards</title>
<link href="https://fonts.googleapis.com/css2?family=Cinzel:wght@600&family=Arimo:wght@400&display=swap" rel="stylesheet">
<style>
  :root {
    --backdrop: #2b2b2d;
    --navy: #1b1f2b;
    --paper: #ffffff;
    --stripe: #a7a7a9;
    --ink-light: #ffffff;
    --ink-muted: #d6d8de;
  }
  * { box-sizing: border-box; margin: 0; padding: 0; }
  html, body {
    width: 1200px; height: 874px; overflow: hidden;
    background: var(--backdrop);
  }
  .sheet {
    width: 1200px; height: 874px;
    display: flex; flex-direction: column; align-items: center; justify-content: center;
    gap: 30px;
  }
  .card {
    width: 700px; height: 400px;
    border-radius: 22px;
    overflow: hidden;
    position: relative;
    box-shadow: 0 14px 30px rgba(0,0,0,.45);
  }
  .card--back {
    background: var(--navy);
    display: flex; align-items: center; justify-content: center;
  }
  .brand {
    display: flex; flex-direction: column; align-items: center; gap: 18px;
  }
  .brand__ring {
    width: 92px; height: 92px; border-radius: 50%;
    border: 3px solid currentColor;
  }
  .brand__name {
    font-family: "Cinzel", serif;
    font-weight: 600;
    font-size: 34px;
    letter-spacing: 1px;
  }
  .card--back .brand { color: var(--ink-light); }

  .card--front { display: flex; background: var(--navy); }
  .front__brand-side {
    width: 340px; background: var(--paper);
    display: flex; align-items: center; justify-content: center;
  }
  .front__brand-side .brand { color: var(--navy); }
  .front__brand-side .brand__name { font-size: 29px; }
  .front__stripe { width: 12px; background: var(--stripe); }
  .front__details {
    flex: 1; padding: 70px 0 0 72px;
    color: var(--ink-light);
    font-family: "Arimo", sans-serif;
  }
  .person__name {
    font-family: "Cinzel", serif; font-weight: 600;
    font-size: 28px; letter-spacing: 1px;
  }
  .person__role { font-size: 15px; color: var(--ink-muted); margin-top: 2px; }
  .address { font-size: 16px; line-height: 1.3; margin-top: 26px; }
  .contacts { list-style: none; margin-top: 14px; font-size: 16px; line-height: 1.35; }
  .contacts li { display: flex; align-items: center; gap: 10px; }
  .contacts svg { width: 14px; height: 14px; fill: var(--ink-light); flex: none; }
</style>
</head>
<body>
<main class="sheet">
  <section class="card card--back">
    <div class="brand">
      <span class="brand__ring"></span>
      <span class="brand__name">Corvane Capital</span>
    </div>
  </section>

  <section class="card card--front">
    <div class="front__brand-side">
      <div class="brand">
        <span class="brand__ring"></span>
        <span class="brand__name">Corvane Capital</span>
      </div>
    </div>
    <div class="front__stripe"></div>
    <div class="front__details">
      <h1 class="person__name">Elliot Marsh</h1>
      <p class="person__role">President</p>
      <p class="address">4120 Alder Court<br>Halden, Canada 21847</p>
      <ul class="contacts">
        <li><svg viewBox="0 0 24 24"><path d="M6.6 10.8a15.1 15.1 0 0 0 6.6 6.6l2.2-2.2c.3-.3.7-.4 1-.2 1.1.4 2.3.6 3.6.6.6 0 1 .4 1 1V20c0 .6-.4 1-1 1A17 17 0 0 1 3 4c0-.6.4-1 1-1h3.5c.6 0 1 .4 1 1 0 1.3.2 2.5.6 3.6.1.3 0 .7-.2 1z"/></svg>555-210-4873</li>
        <li><svg viewBox="0 0 24 24"><path d="M7 1h10a2 2 0 0 1 2 2v18a2 2 0 0 1-2 2H7a2 2 0 0 1-2-2V3a2 2 0 0 1 2-2zm0 3v14h10V4zm5 15.5a1 1 0 1 0 0 2 1 1 0 0 0 0-2z"/></svg>555-310-7926</li>
        <li><svg viewBox="0 0 24 24"><path d="M2 5h20v14H2zm2 2v.5l8 5 8-5V7zm0 2.8V17h16V9.8l-8 5z"/></svg>info@corvanecapital.com</li>
        <li><svg viewBox="0 0 24 24"><path d="M12 2a10 10 0 1 0 0 20 10 10 0 0 0 0-20zm0 2c.9 1.2 1.6 2.6 2 4h-4c.4-1.4 1.1-2.8 2-4zM4.3 14a8 8 0 0 1 0-4h3.4a16 16 0 0 0 0 4zm.8 2h3c.3 1.3.8 2.5 1.4 3.6A8 8 0 0 1 5.1 16zm3-8h-3a8 8 0 0 1 4.4-3.6C7.9 5.5 7.4 6.7 8.1 8zM12 20c-.9-1.2-1.6-2.6-2-4h4c-.4 1.4-1.1 2.8-2 4zm2.3-6H9.7a14 14 0 0 1 0-4h4.6a14 14 0 0 1 0 4zm.2 5.6c.6-1.1 1.1-2.3 1.4-3.6h3a8 8 0 0 1-4.4 3.6zm1.8-5.6a16 16 0 0 0 0-4h3.4a8 8 0 0 1 0 4z"/></svg>www.corvanecapital.com</li>
      </ul>
    </div>
  </section>
</main>
</body>
</html>
```